New Business Card Design Project

Use the flyer uploaded and website www.brightoakbuilders.com for inspiration.
List Our Services on Backside of business cards
Marcus Delling
Harborline Builders Inc.
Licensed General Contractors
858-471-6093

Contact Information for Business Card

Use the flyer uploaded and website www.brightoakbuilders.com for inspiration. List Our Services on Backside of business cards Marcus Delling Harborline Builders Inc. Licensed General Contractors 858-471-6093

```html
<!DOCTYPE html>
<html lang="en">
<head>
<meta charset="UTF-8">
<title>Harborline Builders – Business Card Front</title>
<link rel="stylesheet" href="https://fonts.googleapis.com/css2?family=Cinzel:wght@400&family=Montserrat:wght@300&display=swap">
<style>
  :root {
    --card-black: #121212;
    --band-grey: #c9c9c9;
    --band-blue: #0b4fa6;
    --text-white: #f4f4f4;
  }
  * { margin: 0; padding: 0; box-sizing: border-box; }
  html, body {
    width: 1200px;
    height: 688px;
    overflow: hidden;
    background: var(--card-black);
  }
  .card {
    position: relative;
    width: 1200px;
    height: 688px;
    background: var(--card-black);
    overflow: hidden;
  }
  .card-bands {
    position: absolute;
    inset: 0;
    width: 1200px;
    height: 688px;
  }
  .band-grey { fill: var(--band-grey); }
  .band-blue {
    fill: none;
    stroke: var(--band-blue);
    stroke-width: 24;
    stroke-linejoin: miter;
  }
  .brand {
    position: absolute;
    left: 0;
    width: 1200px;
    top: 400px;
    text-align: center;
    color: var(--text-white);
  }
  .brand-name {
    font-family: "Cinzel", serif;
    font-weight: 400;
    font-size: 40px;
    letter-spacing: 1px;
    line-height: 1;
  }
  .brand-tagline {
    margin-top: 14px;
    font-family: "Montserrat", sans-serif;
    font-weight: 300;
    font-size: 17px;
    letter-spacing: 6px;
    line-height: 1;
  }
</style>
</head>
<body>
  <main class="card">
    <svg class="card-bands" viewBox="0 0 1200 688" aria-hidden="true">
      <polygon class="band-grey" points="0,246 860,0 905,0 0,276"/>
      <polyline class="band-blue" points="44,700 44,300 1040,0"/>
    </svg>
    <div class="brand">
      <h1 class="brand-name">HARBORLINE BUILDERS</h1>
      <p class="brand-tagline">BUILD YOUR DREAM</p>
    </div>
  </main>
</body>
</html>
```